Plakat für Hersteller von maßgefertigten Tischunikaten aus Massivholz
Zielgruppe
Wir sind einen Firma die sich auf die Fertigung von maßgefertigten Tischunikaten aus Massivholz spezialisiert hat. Unsere Zielgruppe sind Design affine Leute, im Alter von 35-55 Jahren
Aufgabenstellung
Wir benötigen das Design für eine Messewand mit den Maßen 443X227 cm. 5 Zentimeter rundlaufen dürfen keine Elemente mehr platziert werden. Die Messewand steht im Hintergrund von unserem Stand bei verschiedenen Designmessen
Infos die auf die Messewand müssen: Logo, Tischmanufaktur aus Stuttgart, Maßgefertigte Tischunikate (Bei der Formulierung bin ich flexibel, ihr könnt bspw. auch nur Stichworte benutzen, aber Stuttgart und maßgefertigt ist wichtig).
Die Messewand soll sehr minimalistisch gestaltet sein, bei der letzten Messewand hatten wir ein Foto von einem Tisch im Hintergrund und das sah merkwürdig aus.

```html
<!DOCTYPE html>
<html lang="de">
<head>
<meta charset="utf-8">
<title>Holmberg Manufaktur – Messewand</title>
<link rel="stylesheet" href="https://fonts.googleapis.com/css2?family=Montserrat:wght@200;600;700&display=swap">
<style>
  :root {
    --page-bg: #e4e4e4;
    --wall-dark: #222222;
    --wall-mid: #2e2e2e;
    --wall-light: #4a4a4a;
    --text-light: #ffffff;
    --accent-green: #537c3f;
  }
  html, body {
    margin: 0;
    width: 1200px;
    height: 816px;
    overflow: hidden;
    background: var(--page-bg);
  }
  .trade-wall {
    position: absolute;
    left: 20px;
    top: 111px;
    width: 1160px;
    height: 594px;
    overflow: hidden;
    color: var(--text-light);
    font-family: "Montserrat", sans-serif;
  }
  .wall-texture {
    position: absolute;
    inset: 0;
    background:
      radial-gradient(ellipse 420px 300px at 0 0, var(--wall-light), transparent 75%),
      linear-gradient(90deg, var(--wall-mid) 0%, var(--wall-dark) 100%);
  }
  .brand-mark {
    position: absolute;
    left: 456px;
    top: 40px;
    width: 76px;
    height: 76px;
  }
  .brand-name {
    position: absolute;
    left: 543px;
    top: 39px;
    margin: 0;
    font-weight: 600;
    font-size: 27px;
    line-height: 31px;
  }
  .headline {
    position: absolute;
    left: 0;
    right: 0;
    margin: 0;
    text-align: center;
    font-weight: 200;
    font-size: 76px;
    line-height: 1;
    letter-spacing: 0.03em;
  }
  .headline-top { top: 150px; }
  .headline-bottom { top: 239px; }
  .location-line {
    position: absolute;
    left: 0;
    right: 0;
    top: 336px;
    margin: 0;
    text-align: center;
    font-weight: 700;
    font-size: 39px;
    line-height: 1;
    letter-spacing: 0.01em;
  }
  .city-tag {
    display: inline-block;
    margin-left: 6px;
    padding: 7px 24px 6px 18px;
    background: var(--accent-green);
    border-radius: 9px;
  }
  .web-address {
    position: absolute;
    left: 0;
    right: 0;
    top: 541px;
    margin: 0;
    text-align: center;
    font-weight: 700;
    font-size: 15px;
    line-height: 1;
    letter-spacing: 0.02em;
  }
</style>
</head>
<body>
  <main class="trade-wall">
    <div class="wall-texture" role="img" aria-label="Dunkler Hintergrund mit feinen grauen Höhenlinien im Stil einer topografischen Karte"></div>

    <svg class="brand-mark" viewBox="0 0 76 76" aria-hidden="true">
      <circle cx="38" cy="38" r="35" fill="none" stroke="var(--text-light)" stroke-width="4"/>
    </svg>
    <p class="brand-name">Holmberg<br>Manufaktur</p>

    <h1 class="headline headline-top">MASSGEFERTIGTE</h1>
    <h1 class="headline headline-bottom">TISCHUNIKATE</h1>

    <p class="location-line">HERSTELLUNG IN <span class="city-tag">STUTTGART</span></p>

    <p class="web-address">WWW.HOLMBERG-MANUFAKTUR.DE</p>
  </main>
</body>
</html>
```